Pellowar

We need logo and wesbsite for a software development company based out of Hyderabad, India focused on startups and mid sized companies focused on build a new software products in USA and Europe countires.

Target Market(s)

startup and midsized companies in teh USA and Europe for software product development.

Industry/Entity Type

software development

Coding

Coded - Design and coding required

Number of Pages Required

5+ page

Requirements
Must have
• latest design concepts and very elegant
Nice to have
• each page should have images that reflects the content
Should not have
• too many colors

```html
<!DOCTYPE html>
<html lang="en">
<head>
<meta charset="utf-8">
<title>Pellowar — Software Product Development</title>
<link rel="stylesheet" href="https://fonts.googleapis.com/css2?family=Josefin+Sans:wght@700&family=Lato:wght@400;700&family=Oxygen:wght@300;400&display=swap">
<style>
:root{
  --orange:#f28c1c;
  --orange-soft:#fbe3c6;
  --ink:#1c1c1c;
  --text:#333333;
  --muted:#555555;
  --band:#f4f4f4;
  --band-soft:#f9f9f9;
  --white:#ffffff;
  --foot:#ebebeb;
}
*{margin:0;padding:0;box-sizing:border-box}
html,body{width:1200px;height:3086px;overflow:hidden}
body{position:relative;background:var(--white);font-family:"Lato",sans-serif;color:var(--text)}
.btn{position:absolute;background:var(--orange);color:var(--white);border-radius:30px;font-size:13px;display:flex;align-items:center;justify-content:center}

/* header */
.site-header{position:absolute;top:0;left:0;width:1200px;height:93px;background:var(--white);box-shadow:0 2px 4px rgba(0,0,0,.05);z-index:2}
.brand{position:absolute;left:98px;top:24px;display:flex;align-items:center;gap:10px}
.brand-dot{width:40px;height:40px;border-radius:50%;background:var(--orange)}
.brand-name{font-weight:700;font-size:34px;color:var(--ink)}
.nav a{position:absolute;top:48px;font-size:13px;color:var(--ink);text-decoration:none}
.nav a.active{color:var(--orange)}
.nav-underline{position:absolute;left:576px;top:88px;width:48px;height:3px;background:var(--orange)}

/* hero */
.hero{position:absolute;top:93px;left:0;width:1200px;height:369px;background:var(--band);box-shadow:0 3px 5px rgba(0,0,0,.06)}
.hero-kicker{position:absolute;left:98px;top:72px;font-family:"Josefin Sans",sans-serif;font-weight:700;font-size:38px;color:var(--orange)}
.hero-title{position:absolute;left:98px;top:117px;font-family:"Josefin Sans",sans-serif;font-weight:700;font-size:39px;color:var(--ink)}
.hero-text{position:absolute;left:101px;top:171px;width:420px;font-size:12.5px;line-height:16.5px;color:var(--ink)}
.hero-photo{position:absolute;left:727px;top:43px;width:292px;height:292px;border-radius:50%;border:4px solid var(--white);background:radial-gradient(circle at 40% 35%,#ececec,#c9c9c9 70%,#b0b0b0)}
.hero-ring{position:absolute;left:716px;top:21px}
.dots{position:absolute;left:584px;top:324px;display:flex;gap:7px}
.dots span{width:10px;height:10px;border-radius:50%;background:#cfcfcf}
.dots span.on{background:var(--orange)}

/* sections */
.section-title{position:absolute;font-family:"Oxygen",sans-serif;font-weight:300;color:var(--ink);text-align:center;left:0;width:1200px}
.rule{position:absolute;left:533px;width:134px;height:3px;background:var(--orange)}
.copy{position:absolute;left:0;width:1200px;text-align:center;font-size:14px;line-height:19px;color:var(--text)}
.product{position:absolute;top:889px;left:0;width:1200px;height:917px;background:var(--band)}
.team{position:absolute;top:1806px;left:0;width:1200px;height:894px;background:var(--band-soft)}

/* roadmap illustration area */
.roadmap{position:absolute;left:216px;top:1172px;width:768px;height:420px;border-radius:8px;background:linear-gradient(120deg,var(--band) 0%,var(--orange-soft) 50%,var(--band) 100%)}

/* cards */
.card{position:absolute;top:2212px;width:308px;height:392px;background:var(--white);box-shadow:0 1px 6px rgba(0,0,0,.1);overflow:hidden}
.card-photo{position:absolute;left:10px;top:10px;width:288px;height:161px;background:linear-gradient(135deg,#6b5443 0%,#b7a592 40%,#d9d4cc 70%,#a9b8a3 100%)}
.card-num{position:absolute;left:0;top:-3px;width:59px;height:59px;background:var(--orange);color:var(--white);font-family:"Oxygen",sans-serif;font-weight:300;font-size:36px;display:flex;align-items:center;justify-content:center}
.card-title{position:absolute;left:17px;top:194px;font-family:"Oxygen",sans-serif;font-weight:400;font-size:18px;line-height:24px;color:var(--ink)}
.card-rule{position:absolute;left:17px;top:246px;width:28px;height:2px;background:var(--orange)}
.card-text{position:absolute;left:17px;top:265px;width:240px;font-size:12px;line-height:16px;color:var(--muted)}
.card .btn{left:17px;top:326px;width:96px;height:32px;font-size:12px}
.card-corner{position:absolute;right:0;bottom:0;width:0;height:0;border-left:24px solid transparent;border-bottom:24px solid var(--orange)}

/* footer */
.site-footer{position:absolute;top:2700px;left:0;width:1200px;height:302px;background:var(--white)}
.foot-brand-dot{position:absolute;left:150px;top:58px;width:126px;height:126px;border-radius:50%;background:var(--orange)}
.foot-brand{position:absolute;left:93px;top:184px;font-weight:700;font-size:46px;color:var(--ink)}
.foot-head{position:absolute;top:50px;font-family:"Oxygen",sans-serif;font-weight:400;font-size:22px;color:var(--ink)}
.foot-rule{position:absolute;top:82px;width:44px;height:2px;background:var(--orange)}
.links{position:absolute;left:444px;top:98px;list-style:none}
.links li{font-size:12px;line-height:23.5px;color:var(--ink)}
.links li::before{content:"»";color:var(--orange);margin-right:8px}
.contact{position:absolute;left:752px;top:102px}
.contact-item{position:relative;padding-left:20px;margin-bottom:9px}
.contact-item svg{position:absolute;left:0;top:2px}
.contact-item b{display:block;font-size:13px;line-height:20px;color:var(--ink)}
.contact-item span{display:block;font-size:13.5px;line-height:20px;color:var(--text)}
.copyright{position:absolute;top:3002px;left:0;width:1200px;height:84px;background:var(--foot);text-align:center;font-size:11px;letter-spacing:5px;line-height:84px;color:var(--muted)}
</style>
</head>
<body>

<header class="site-header">
  <div class="brand"><span class="brand-dot"></span><span class="brand-name">Pellowar</span></div>
  <nav class="nav">
    <a class="active" style="left:584px">Home</a>
    <a style="left:641px">About Us</a>
    <a style="left:717px">Build Your Product</a>
    <a style="left:845px">Build Your team</a>
    <a style="left:957px">Case Study</a>
    <a style="left:1041px">Contact Us</a>
  </nav>
  <div class="nav-underline"></div>
</header>

<section class="hero">
  <div class="hero-kicker">Lets Transform Your</div>
  <div class="hero-title">Visions &amp; Goals Into Reality</div>
  <p class="hero-text">Break free from traditional recruiting with us. At Pellowar, we help you achieve the right organizational matrix with rockstars who can take your business to the next level.</p>
  <a class="btn" style="left:98px;top:245px;width:140px;height:43px">Know More</a>
  <svg class="hero-ring" width="336" height="336" viewBox="0 0 336 336">
    <circle cx="168" cy="168" r="160" fill="none" stroke="var(--orange)" stroke-width="13" stroke-dasharray="720 285" transform="rotate(-100 168 168)"/>
  </svg>
  <div class="hero-photo" role="img" aria-label="Laptop, glasses and earbuds on a marble desk"></div>
  <div class="dots"><span class="on"></span><span></span><span></span><span></span><span></span></div>
</section>

<section class="about">
  <h2 class="section-title" style="top:522px;font-size:56px">About Us</h2>
  <div class="rule" style="top:598px"></div>
  <p class="copy" style="top:634px;font-weight:700;color:var(--ink)">Teams are the essence of every business. They can create wonders if built with perfection.</p>
  <p class="copy" style="top:672px;left:225px;width:750px">We are a group of entrepreneurs, technocrats, software architects, and delivery heads who have come together to serve startups, product companies, and enterprises with their product development. We are prompt in understanding your product and help design, build, maintain and operate your product. Pellowar quickly set up a team of UX experts, Business Analysts, Developers and QA resources to build the best team to deliver the product.</p>
  <a class="btn" style="left:531px;top:773px;width:138px;height:43px">Read More</a>
</section>

<section class="product">
  <h2 class="section-title" style="top:44px;font-size:58px">Build Your Product</h2>
  <div class="rule" style="top:140px"></div>
  <p class="copy" style="top:176px;left:255px;width:690px">As startups are racing to build software as a product, they have stumbling blocks on building software from scratch. One of the reasons is stiff competition.<br>The competition to get the best resources, robust design, and scalable technology is overwhelming.</p>
  <p class="copy" style="top:764px;left:250px;width:700px">This approach gives more flexibility, allowing for the full-scale product concept review without spending your budget on something nobody will use</p>
  <a class="btn" style="left:531px;top:833px;width:138px;height:43px">Read More</a>
</section>

<div class="roadmap" role="img" aria-label="Winding ten-step roadmap: spot the problem, interview users, discuss findings, research, mockups, test designs, iterate prototypes, build MVP, distribute to early adopters, analyze feedback"></div>

<section class="team">
  <h2 class="section-title" style="top:44px;font-size:58px">Build Your Team</h2>
  <div class="rule" style="top:137px"></div>
  <p class="copy" style="top:188px;left:260px;width:680px">Break free from traditional recruiting with us. At Pellowar, we help you achieve the right organizational matrix with rockstars who can take your business to the next level.</p>
  <p class="copy" style="top:244px;left:255px;width:690px">We have spent years trying to innovate and improve the process of hiring talented individuals who can take businesses to the next level. We ensure that the workforce we employ for your organization is highly productive and takes you to the golden standards of heights.</p>
  <p class="copy" style="top:320px;font-weight:700;color:var(--ink)">The 3 stages of hiring</p>
</section>

<article class="card" style="left:98px">
  <div class="card-photo" role="img" aria-label="Hands typing on a laptop at an office desk"></div>
  <div class="card-num">01</div>
  <h3 class="card-title">Know why you are hiring<br>a resource</h3>
  <div class="card-rule"></div>
  <p class="card-text">If you do not know why you want to interview and hire a software engineer, understand that you can ...</p>
  <a class="btn">Read More</a>
  <span class="card-corner"></span>
</article>
<article class="card" style="left:443px">
  <div class="card-photo" role="img" aria-label="Hands typing on a laptop at an office desk"></div>
  <div class="card-num">02</div>
  <h3 class="card-title">The interview<br>process</h3>
  <div class="card-rule"></div>
  <p class="card-text">If you do not know why you want to interview and hire a software engineer, understand that you can ...</p>
  <a class="btn">Read More</a>
  <span class="card-corner"></span>
</article>
<article class="card" style="left:792px">
  <div class="card-photo" role="img" aria-label="Hands typing on a laptop at an office desk"></div>
  <div class="card-num">03</div>
  <h3 class="card-title">Giving real-life<br>assessments</h3>
  <div class="card-rule"></div>
  <p class="card-text">If you do not know why you want to interview and hire a software engineer, understand that you can ...</p>
  <a class="btn">Read More</a>
  <span class="card-corner"></span>
</article>

<footer class="site-footer">
  <div class="foot-brand-dot"></div>
  <div class="foot-brand">Pellowar</div>
  <h4 class="foot-head" style="left:443px">Main Links</h4>
  <div class="foot-rule" style="left:443px"></div>
  <ul class="links">
    <li>Home</li><li>About Us</li><li>Our Products</li><li>Our Team</li><li>Case Study</li><li>Contact Us</li>
  </ul>
  <h4 class="foot-head" style="left:752px">Contact Us</h4>
  <div class="foot-rule" style="left:752px"></div>
  <div class="contact">
    <div class="contact-item">
      <svg width="12" height="15" viewBox="0 0 12 15"><path d="M6 0a6 6 0 0 0-6 6c0 4 6 9 6 9s6-5 6-9a6 6 0 0 0-6-6z" fill="var(--orange)"/><circle cx="6" cy="6" r="2.2" fill="var(--white)"/></svg>
      <b>Address:</b><span>48 Harlow Lane Dunmore, TX 41820</span>
    </div>
    <div class="contact-item">
      <svg width="14" height="14" viewBox="0 0 14 14"><path d="M3 1l2.5 3-1.5 2a8 8 0 0 0 4 4l2-1.5 3 2.5-1.5 2C6 13 1 8 1 2.5z" fill="var(--orange)"/></svg>
      <b>Phone:</b><span>1-800-555-01-42</span>
    </div>
    <div class="contact-item">
      <svg width="15" height="11" viewBox="0 0 15 11"><rect width="15" height="11" rx="1" fill="var(--orange)"/><path d="M1 1.5l6.5 5 6.5-5" fill="none" stroke="var(--white)" stroke-width="1.3"/></svg>
      <b>Mail:</b><span>hello@pellowar.com</span>
    </div>
  </div>
</footer>
<div class="copyright">COPYRIGHT © 2022 PELLOWAR</div>

</body>
</html>
```